WTF!!! We need a modern professional website for a business litigation law firm.

We need a modern, clean, professional and uncomplicated website for a new business trial and litigation law firm called "Haverlock Trial Firm PLLC". Website must be mobile optimized for iPad and smartphone. The law firm specializes in counseling and representing large corporations, small businesses and entrepreneurs in and out of the courtroom. Lawyers in the firm serve as Florida counsel and trial counsel to organizations facing claims involving product liability, premises liability, professional liability, vehicle and transportation liability, warranty claims, construction defects and delay claims, complex business disputes, commercial litigation and bid disputes in State and Federal Courts. The website is mainly to provide information about the firm, and should include sections describing the firm, identifying the Industries Served and Areas of Practice ," a separate page identifying the "Professionals", a separate page for "Resources & Advisories," and a traveling "Connect With Us" button a site visitor can click on that will launch an email to the Firm's general email account. The website should allow us to easily modify the content on these pages, and let us add/modify links to external information sources. We will not sell anything or take payments through the website. We do need to be able to easily upload and update photographs of attorneys and add new attorneys names/email hyperlinks as the firm grows. We would like to add developments in the law or success stories easily and quickly, such as through a blog page. On the "Connect With Us" page the website should have hyperlinks to email the Firm, and there should be hyperlinks to email each professional on the "Professionals" page. The website should be viewable on mobile devices without distortion. The law firm focuses on trial work and should have some imagery associated with courtrooms, but the overall theme of the site should be modern, clean, and communicate sophistication and strength. The website should be made in Wordpress. We have uploaded logo files for Haverlock Trial Firm.

Target Market(s)

Corporations and companies that are looking for legal representation. Other attorneys/legal industry.

Industry/Entity Type

Legal Industry

Coding

Coded - Design and coding required

Number of Pages Required

1 page

Font styles to use
Sans Serif

Requirements
Must have
• Simple, clean, sophisticated, modern website that includes the logo, watermark of logo, and the elements described above.
Nice to have
• Pictures of city scape, buildings, courtroom, team members.

```html
<!DOCTYPE html>
<html lang="en">
<head>
<meta charset="utf-8">
<title>Haverlock Trial Firm PLLC</title>
<link rel="stylesheet" href="https://fonts.googleapis.com/css2?family=Poppins:ital,wght@0,400;0,500;0,600;0,700;1,400&family=Playfair+Display:wght@500;600;700&family=Montserrat:wght@700;800&display=swap">
<style>
:root{
  --gold:#c9945a;
  --blue:#1a8cff;
  --ink:#1b1b1b;
  --text:#555;
  --muted:#8a8a8a;
  --light:#f2f2f2;
  --line:#d8d8d8;
  --white:#fff;
  --black:#050505;
}
*{box-sizing:border-box;margin:0;padding:0}
html,body{width:1200px;height:4702px;overflow:hidden}
body{position:relative;font-family:"Poppins",sans-serif;color:var(--text);background:var(--white)}
.abs{position:absolute}
section{position:absolute;left:0;width:1200px}
.serif{font-family:"Playfair Display",serif}

/* hero */
.hero{top:0;height:612px;background:linear-gradient(180deg,#2d2f3e 0%,#4a4a5c 35%,#5b3b2e 70%,#1d1d22 100%)}
.hero-shade{position:absolute;inset:0;background:linear-gradient(90deg,rgba(10,12,20,.65) 0%,rgba(10,12,20,.25) 60%,rgba(10,12,20,.1) 100%)}
.brand{position:absolute;color:var(--white);font-family:"Montserrat",sans-serif;font-weight:800;line-height:1.05;letter-spacing:.5px}
.brand .sq{display:inline-block;width:12px;height:12px;background:var(--white);margin-right:8px;vertical-align:middle}
.contact-item{position:absolute;top:33px;display:flex;gap:12px;color:var(--white);font-size:12px;line-height:1.25}
.contact-item .ic{width:34px;height:34px;border:1px solid rgba(255,255,255,.7);border-radius:3px;display:flex;align-items:center;justify-content:center}
.contact-item small{display:block;font-size:11px;letter-spacing:.5px}
.contact-item b{font-weight:600;font-size:13px}
.btn-connect{left:891px;top:33px;width:167px;height:37px;background:var(--blue);color:var(--white);font-size:12px;font-weight:600;letter-spacing:.6px;display:flex;align-items:center;justify-content:center}
.nav{top:124px;display:flex;font-size:11.5px;font-weight:500;color:var(--white);letter-spacing:.3px}
.nav a{position:absolute;white-space:nowrap;color:var(--white);text-decoration:none}
.nav a.active{color:var(--blue)}
.hero h1{left:141px;top:218px;font-family:"Montserrat",sans-serif;font-weight:800;font-size:40px;line-height:51px;color:var(--white);letter-spacing:.5px}
.hero p{left:141px;top:381px;font-size:18px;color:var(--white)}
.btn-learn{left:141px;top:435px;width:140px;height:45px;background:var(--blue);color:var(--white);font-size:12px;font-weight:600;letter-spacing:.8px;display:flex;align-items:center;justify-content:center;border-bottom:3px solid #0d5fb3}

/* shared */
.sec-title{width:1200px;left:0;text-align:center;font-family:"Playfair Display",serif;font-weight:600;font-size:38px;color:var(--ink)}
.sec-title span,.about-title span{color:var(--gold)}
.divider{display:flex;align-items:center;gap:8px}
.divider i{display:block;width:36px;height:1px;background:var(--gold)}
.divider b{display:block;width:10px;height:10px;background:var(--ink)}
.sec-sub{width:1200px;left:0;text-align:center;font-size:13px;line-height:22px;color:var(--text)}
.btn-gold{height:37px;background:var(--gold);color:var(--white);font-size:13px;font-weight:600;border-radius:20px;display:flex;align-items:center;justify-content:center}
.arrow{width:28px;height:28px;border-radius:50%;display:flex;align-items:center;justify-content:center}
.arrow.out{border:1px solid var(--gold)}
.arrow.fill{background:var(--gold)}

/* about */
.about{top:612px;height:581px}
.about-title{left:141px;top:70px;font-family:"Playfair Display",serif;font-weight:600;font-size:40px;color:var(--ink)}
.about .lead{left:141px;top:160px;width:420px;font-size:13px;font-weight:600;color:var(--ink);line-height:22px}
.about .para{left:141px;width:430px;font-size:13px;line-height:22.5px}
.photo{position:absolute}

/* practice */
.practice{top:1193px;height:613px;background:var(--light)}
.p-card{position:absolute;top:241px;width:287px;height:195px;background:var(--white);padding:28px 24px}
.p-card h3{font-family:"Playfair Display",serif;font-size:13px;font-weight:700;color:var(--ink)}
.p-card p{margin-top:40px;font-size:12px;line-height:20px;width:215px}
.p-card svg{position:absolute;right:24px;top:20px}

/* industries */
.industries{top:1806px;height:729px}
.hub{left:482px;top:247px;width:212px;height:212px;border-radius:50%;background:var(--white);box-shadow:0 0 30px rgba(0,0,0,.08);display:flex;flex-direction:column;align-items:center;justify-content:center;font-family:"Montserrat",sans-serif;font-weight:800;color:var(--ink);font-size:22px;line-height:1.1;text-align:center}
.orbit{left:428px;top:193px;width:320px;height:320px;border-radius:50%;border:1.5px dashed #d8d8d8}
.ind-ic{position:absolute;width:46px;height:46px;border-radius:50%;background:var(--white);box-shadow:0 2px 10px rgba(0,0,0,.08);display:flex;align-items:center;justify-content:center}
.ind{position:absolute;width:260px;font-size:12px;line-height:20px}
.ind h4{font-family:"Playfair Display",serif;font-size:13px;font-weight:700;color:var(--ink);margin-bottom:6px}
.ind.r{text-align:right}
.ind.c{text-align:center}

/* clients */
.clients{top:2535px;height:605px;background:var(--light)}
.t-card{position:absolute;top:243px;width:446px;height:230px;background:var(--white);padding:28px}
.avatar{position:absolute;left:28px;top:28px;width:68px;height:68px;border-radius:50%}
.t-card h4{position:absolute;left:112px;top:42px;font-family:"Playfair Display",serif;font-size:14px;font-weight:700;color:var(--ink)}
.t-card small{position:absolute;left:112px;top:66px;font-size:11.5px}
.t-card .q{position:absolute;right:40px;top:0;font-family:"Playfair Display",serif;font-size:120px;color:#e6e6e6;line-height:1}
.t-card p{position:absolute;left:28px;right:40px;top:118px;font-size:12.5px;font-style:italic;line-height:23px;text-align:justify}
.dots{left:570px;top:3048px;display:flex;gap:4px;align-items:center}
.dots i{display:block;width:7px;height:7px;border-radius:50%;background:#c9c9c9}
.dots i.on{width:10px;height:10px;background:var(--gold)}

/* resources */
.resources{top:3140px;height:1134px}
.r-img{position:absolute;top:241px;width:290px;height:228px}
.r-box{position:absolute;top:436px;width:246px;height:126px;background:var(--white);box-shadow:0 4px 18px rgba(0,0,0,.08);text-align:center;padding-top:14px}
.r-box .date{font-size:11px;color:var(--ink);display:flex;gap:6px;justify-content:center;align-items:center}
.r-box h4{margin-top:8px;font-family:"Playfair Display",serif;font-size:12.5px;font-weight:700;color:var(--ink);line-height:22px}
.r-box a{display:inline-block;margin-top:6px;font-size:12px;font-weight:500;color:var(--gold);text-decoration:none;border-bottom:1px solid var(--gold)}

/* contact */
.contact{left:141px;top:3863px;width:918px;height:566px;background:var(--white);box-shadow:0 6px 30px rgba(0,0,0,.08);z-index:2}
.field{position:absolute;width:317px;border-bottom:1px solid #999;font-size:11px;color:var(--muted);padding:0 10px 6px}
.field.dark{border-bottom:2px solid var(--ink);color:var(--ink)}

/* footer */
.footer{top:4274px;height:428px;background:var(--black);color:#d6d6d6}
.footer h5{position:absolute;top:210px;font-family:"Playfair Display",serif;font-size:13px;font-weight:600;color:var(--white)}
.footer ul{position:absolute;top:250px;list-style:none;font-size:11.5px;line-height:25.5px;color:var(--white)}
.footer ul li::before{content:"•";margin-right:8px}
.f-row{position:absolute;left:884px;display:flex;gap:12px;font-size:12px;color:var(--white);line-height:20px}
.social{position:absolute;top:393px;left:966px;display:flex;gap:9px}
.social i{display:block;width:19px;height:19px;border:1px solid #bbb;border-radius:50%}
</style>
</head>
<body>

<!-- HERO -->
<section class="hero">
  <div class="abs" style="inset:0" role="img" aria-label="Dusk cityscape with government towers and historic buildings"></div>
  <div class="hero-shade"></div>
  <div class="brand" style="left:141px;top:30px;font-size:20px">HAVERLOCK<br><span style="font-size:20px">TRIAL FIRM</span></div>
  <div class="contact-item" style="left:447px">
    <div class="ic"><svg width="16" height="16" viewBox="0 0 24 24" fill="none" stroke="#fff" stroke-width="2"><path d="M5 3h4l2 5-3 2a11 11 0 0 0 6 6l2-3 5 2v4a2 2 0 0 1-2 2A17 17 0 0 1 3 5a2 2 0 0 1 2-2z"/></svg></div>
    <div><small>PHONE</small><b>123-456-7890</b></div>
  </div>
  <div class="contact-item" style="left:617px">
    <div class="ic"><svg width="16" height="14" viewBox="0 0 24 20" fill="none" stroke="#fff" stroke-width="2"><rect x="2" y="2" width="20" height="16"/><path d="M2 3l10 8 10-8"/></svg></div>
    <div><small>EMAIL</small><b style="font-weight:500">info@haverlocktrialfirm.com</b></div>
  </div>
  <div class="abs btn-connect">CONNECT WITH US</div>
  <nav class="abs nav">
    <a class="active" style="left:163px">HOME</a>
    <a style="left:248px">ABOUT US</a>
    <a style="left:362px">PROFESSIONALS</a>
    <a style="left:517px">INDUSTRIES SERVED</a>
    <a style="left:692px">AREAS OF PRACTICE</a>
    <a style="left:871px">RESOURCES &amp; ADVISORIES</a>
  </nav>
  <h1 class="abs">YOUR TRUSTED<br>PARTNER IN BUSINESS<br>LITIGATION</h1>
  <p class="abs">Expert Counsel for Corporations and Entrepreneurs.</p>
  <div class="abs btn-learn">LEARN MORE</div>
</section>

<!-- ABOUT -->
<section class="about">
  <h2 class="abs about-title">About <span>Haverlock</span></h2>
  <div class="abs divider" style="left:141px;top:127px"><b></b><i></i></div>
  <p class="abs lead">Lorem Ipsum Dolor Sit Amet, Consectetur Adipiscing Elit. Donec Consequat Finibus Augue</p>
  <p class="abs para" style="top:218px">Cras Eu Est Molestie, Vehicula Ipsum Scelerisque, Mattis Lorem. Quisque Sodales Gravida Diam. Suspendisse Nulla Dolor, Placerat Id Tempus Vitae, Ultricies Eget Nisl.</p>
  <p class="abs para" style="top:296px">Vivamus Vestibulum Dolor Eu Massa Blandit Luctus. Sed Molestie, Leo Eget Placerat Mollis, Leo Tortor Tristique Eros, Eu Sollicitudin Ligula Odio Non Enim. Pellentesque Mollis Magna Odio, In Condimentum Dui Feugiat Eleifend. Praesent Eget Neque Nec Mi Finibus Finibus. Aliquam Nec Porta Justo, Sed Accumsan Urna. Nam Non Est Elit.</p>
  <div class="abs btn-gold" style="left:141px;top:458px;width:126px">Learn More</div>
  <div class="photo" style="left:606px;top:106px;width:256px;height:146px;background:linear-gradient(135deg,#9a9a9a,#3a3d44)" role="img" aria-label="Attorney in a suit reviewing documents in an office"></div>
  <div class="photo" style="left:873px;top:144px;width:113px;height:110px;background:linear-gradient(135deg,#c9b8a3,#6b4f3a)" role="img" aria-label="Hand signing a legal document"></div>
  <div class="photo" style="left:643px;top:267px;width:148px;height:211px;background:linear-gradient(180deg,#8e9aa6,#2b3038)" role="img" aria-label="Team of three attorneys standing outside a building"></div>
  <div class="photo" style="left:804px;top:267px;width:255px;height:146px;background:linear-gradient(135deg,#3b3b3b,#1a1a1a 60%,#8a7a66)" role="img" aria-label="Coffee cup on a desk beside legal books"></div>
  <div class="photo" style="left:880px;top:438px;width:160px;height:143px;background:radial-gradient(circle,rgba(201,148,90,.12),rgba(201,148,90,0) 70%)" role="img" aria-label="Faint line drawing of scales of justice"></div>
</section>

<!-- AREAS OF PRACTICE -->
<section class="practice">
  <h2 class="abs sec-title" style="top:70px">Areas Of <span>Practice</span></h2>
  <div class="abs divider" style="left:566px;top:130px"><i></i><b></b><i></i></div>
  <p class="abs sec-sub" style="top:160px">Cras Eu Est Molestie, Vehicula Ipsum Scelerisque, Mattis Lorem. Quisque Sodales Gravida<br>Diam. Suspendisse Nulla Dolor, Placerat Id Tempus Vitae, Ultricies Eget Nisl.</p>
  <div class="abs arrow out" style="left:77px;top:325px"><svg width="8" height="10" viewBox="0 0 8 10"><path d="M6 1L2 5l4 4" stroke="#c9945a" stroke-width="1.5" fill="none"/></svg></div>
  <div class="abs arrow fill" style="left:1093px;top:325px"><svg width="8" height="10" viewBox="0 0 8 10"><path d="M2 1l4 4-4 4" stroke="#fff" stroke-width="1.5" fill="none"/></svg></div>
  <div class="p-card" style="left:141px"><h3>Product Liability</h3>
    <svg width="32" height="34" viewBox="0 0 32 34" fill="none" stroke="#c9945a" stroke-width="1.5"><rect x="5" y="3" width="22" height="28" rx="2"/><path d="M10 10h12M10 15h12M10 20h7"/><circle cx="22" cy="24" r="4"/></svg>
    <p>It is a long established fact that a reader will be distracted by the readable content of a page when looking.</p></div>
  <div class="p-card" style="left:457px"><h3>Remises Liability</h3>
    <svg width="36" height="34" viewBox="0 0 36 34" fill="none" stroke="#c9945a" stroke-width="1.5"><rect x="4" y="6" width="20" height="24" rx="2"/><path d="M9 13h10M9 18h10M9 23h6"/><circle cx="27" cy="10" r="6"/><path d="M25 10l2 2 3-4"/></svg>
    <p>It is a long established fact that a reader will be distracted by the readable content of a page when looking.</p></div>
  <div class="abs arrow fill" style="left:586px;top:424px;width:34px;height:34px"><svg width="12" height="10" viewBox="0 0 12 10"><path d="M1 5h9M7 2l3 3-3 3" stroke="#fff" stroke-width="1.5" fill="none"/></svg></div>
  <div class="p-card" style="left:773px"><h3>Professional Liability</h3>
    <svg width="32" height="34" viewBox="0 0 32 34" fill="none" stroke="#c9945a" stroke-width="1.5"><circle cx="16" cy="12" r="8"/><path d="M12 12l3 3 5-6M8 30c2-6 14-6 16 0"/></svg>
    <p>It is a long established fact that a reader will be distracted by the readable content of a page when looking.</p></div>
  <div class="abs btn-gold" style="left:548px;top:491px;width:104px">View All</div>
</section>

<!-- INDUSTRIES -->
<section class="industries">
  <h2 class="abs sec-title" style="top:70px">Industries We <span>Served</span></h2>
  <div class="abs divider" style="left:566px;top:130px"><i></i><b></b><i></i></div>
  <p class="abs sec-sub" style="top:160px">Cras Eu Est Molestie, Vehicula Ipsum Scelerisque, Mattis Lorem. Quisque Sodales Gravida<br>Diam. Suspendisse Nulla Dolor, Placerat Id Tempus Vitae, Ultricies Eget Nisl.</p>
  <div class="abs orbit"></div>
  <div class="abs hub"><span>HAVERLOCK</span><span style="font-size:11px;letter-spacing:3px;margin-top:4px">TRIAL FIRM</span></div>

  <div class="ind-ic" style="left:426px;top:257px"><svg width="24" height="24" viewBox="0 0 24 24" fill="none" stroke="#c9945a" stroke-width="1.4"><path d="M3 21h18M5 21V9l7-5 7 5v12M9 21v-6h6v6"/></svg></div>
  <div class="ind-ic" style="left:708px;top:257px"><svg width="24" height="24" viewBox="0 0 24 24" fill="none" stroke="#c9945a" stroke-width="1.4"><rect x="2" y="8" width="12" height="9"/><path d="M14 11h4l3 3v3h-7"/><circle cx="6" cy="18" r="2"/><circle cx="17" cy="18" r="2"/></svg></div>
  <div class="ind-ic" style="left:432px;top:421px"><svg width="24" height="24" viewBox="0 0 24 24" fill="none" stroke="#c9945a" stroke-width="1.4"><path d="M4 9h16v12H4zM3 9l2-5h14l2 5M10 21v-5h4v5"/></svg></div>
  <div class="ind-ic" style="left:693px;top:421px"><svg width="24" height="24" viewBox="0 0 24 24" fill="none" stroke="#c9945a" stroke-width="1.4"><path d="M3 21h18M6 21V7h6v14M12 11h6v10M8 10h2M8 14h2M14 14h2"/></svg></div>
  <div class="ind-ic" style="left:565px;top:492px"><svg width="24" height="24" viewBox="0 0 24 24" fill="none" stroke="#c9945a" stroke-width="1.4"><rect x="3" y="7" width="18" height="13" rx="1"/><path d="M9 7V4h6v3M3 12h18"/></svg></div>

  <div class="ind r" style="left:136px;top:240px"><h4>Large Corporations</h4>It is a long established fact that a reader will be distracted by the readable content of a page when looking.</div>
  <div class="ind" style="left:785px;top:240px"><h4>Transportation &amp; Logistics</h4>It is a long established fact that a reader will be distracted by the readable content of a page when looking.</div>
  <div class="ind r" style="left:144px;top:404px"><h4>Small Businesses</h4>It is a long established fact that a reader will be distracted by the readable content of a page when looking.</div>
  <div class="ind" style="left:769px;top:404px"><h4>Construction &amp; Real Estate</h4>It is a long established fact that a reader will be distracted by the readable content of a page when looking.</div>
  <div class="ind c" style="left:458px;top:570px"><h4>Entrepreneurs &amp; Startups</h4>It is a long established fact that a reader will be distracted by the readable content of a page when looking.</div>
</section>

<!-- CLIENTS -->
<section class="clients">
  <h2 class="abs sec-title" style="top:86px">What Our <span>Clients Say</span></h2>
  <div class="abs divider" style="left:566px;top:146px"><i></i><b></b><i></i></div>
  <p class="abs sec-sub" style="top:175px">Cras Eu Est Molestie, Vehicula Ipsum Scelerisque, Mattis Lorem. Quisque Sodales Gravida<br>Diam. Suspendisse Nulla Dolor, Placerat Id Tempus Vitae, Ultricies Eget Nisl.</p>
  <div class="abs arrow out" style="left:77px;top:344px"><svg width="8" height="10" viewBox="0 0 8 10"><path d="M6 1L2 5l4 4" stroke="#c9945a" stroke-width="1.5" fill="none"/></svg></div>
  <div class="abs arrow fill" style="left:1093px;top:344px"><svg width="8" height="10" viewBox="0 0 8 10"><path d="M2 1l4 4-4 4" stroke="#fff" stroke-width="1.5" fill="none"/></svg></div>
  <div class="t-card" style="left:141px">
    <div class="avatar" style="background:linear-gradient(135deg,#d9c4b1,#7a5a48)" role="img" aria-label="Client portrait"></div>
    <h4>John Die</h4><small>CEO At Lorem</small><span class="q">&rdquo;</span>
    <p>" Suspendisse lobortis semper mi in hendrerit. Proin eros nisi, faucibus in suscipit at, rutrum vel metus. Mauris faucibus odio gravida bibendum dignissim. Nulla vitae finibus velit, in bibendum quam. "</p>
  </div>
  <div class="t-card" style="left:615px">
    <div class="avatar" style="background:linear-gradient(135deg,#e8dccb,#a88f74)" role="img" aria-label="Client portrait"></div>
    <h4>Ariadne</h4><small>CEO At Lorem</small><span class="q">&rdquo;</span>
    <p>" Suspendisse lobortis semper mi in hendrerit. Proin eros nisi, faucibus in suscipit at, rutrum vel metus. Mauris faucibus odio gravida bibendum dignissim. Nulla vitae finibus velit, in bibendum quam. "</p>
  </div>
</section>
<div class="abs dots"><i></i><i></i><i class="on"></i><i></i><i></i></div>

<!-- RESOURCES -->
<section class="resources">
  <h2 class="abs sec-title" style="top:75px">Resources &amp; <span>Advisories</span></h2>
  <div class="abs divider" style="left:566px;top:135px"><i></i><b></b><i></i></div>
  <p class="abs sec-sub" style="top:164px">Cras Eu Est Molestie, Vehicula Ipsum Scelerisque, Mattis Lorem. Quisque Sodales Gravida<br>Diam. Suspendisse Nulla Dolor, Placerat Id Tempus Vitae, Ultricies Eget Nisl.</p>
  <div class="abs arrow out" style="left:77px;top:388px"><svg width="8" height="10" viewBox="0 0 8 10"><path d="M6 1L2 5l4 4" stroke="#c9945a" stroke-width="1.5" fill="none"/></svg></div>
  <div class="abs arrow fill" style="left:1093px;top:388px"><svg width="8" height="10" viewBox="0 0 8 10"><path d="M2 1l4 4-4 4" stroke="#fff" stroke-width="1.5" fill="none"/></svg></div>

  <div class="r-img" style="left:141px;background:linear-gradient(180deg,#dfe4ea,#7b8691)" role="img" aria-label="Business team meeting in a bright office"></div>
  <div class="r-img" style="left:455px;background:linear-gradient(135deg,#4a4a4a,#1c1c1c 60%,#a5916f)" role="img" aria-label="Hands holding a legal document"></div>
  <div class="r-img" style="left:769px;background:linear-gradient(135deg,#2b2622,#6e5a44 70%,#a58b66)" role="img" aria-label="Lady Justice statue with books"></div>

  <div class="r-box" style="left:163px"><div class="date"><svg width="11" height="11" viewBox="0 0 12 12" fill="none" stroke="#555"><rect x="1" y="2" width="10" height="9"/><path d="M1 5h10"/></svg>23 Jan2025</div><h4>Lorem Ipsum Dolor Sit Amet,<br>Consectetur Adipiscing Elit...</h4><a>Read More</a></div>
  <div class="r-box" style="left:477px"><div class="date"><svg width="11" height="11" viewBox="0 0 12 12" fill="none" stroke="#555"><rect x="1" y="2" width="10" height="9"/><path d="M1 5h10"/></svg>23 Jan2025</div><h4>Lorem Ipsum Dolor Sit Amet,<br>Consectetur Adipiscing Elit...</h4><a>Read More</a></div>
  <div class="r-box" style="left:791px"><div class="date"><svg width="11" height="11" viewBox="0 0 12 12" fill="none" stroke="#555"><rect x="1" y="2" width="10" height="9"/><path d="M1 5h10"/></svg>23 Jan2025</div><h4>Lorem Ipsum Dolor Sit Amet,<br>Consectetur Adipiscing Elit...</h4><a>Read More</a></div>

  <div class="abs btn-gold" style="left:548px;top:599px;width:104px">View All</div>
</section>

<!-- FOOTER -->
<section class="footer">
  <div class="brand" style="left:141px;top:188px;font-size:18px">HAVERLOCK<br>TRIAL FIRM</div>
  <p class="abs" style="left:141px;top:290px;width:300px;font-size:11.5px;line-height:20px;color:var(--white)">Cras eu est molestie, vehicula ipsum scelerisque, mattis lorem. Quisque sodales gravida diam. Suspendisse nulla dolor, placerat id tempusl.</p>
  <h5 style="left:493px">Quick Links</h5>
  <ul style="left:493px"><li>Home</li><li>About Us</li><li>Areas of Practice</li><li>Our Professionals</li></ul>
  <h5 style="left:678px">Useful Links</h5>
  <ul style="left:678px"><li>Resources &amp; Advisories</li><li>Contact Us</li><li>Privacy Policy</li><li>Terms &amp; Conditions</li></ul>
  <h5 style="left:884px">Stay In Touch</h5>
  <div class="f-row" style="top:248px"><svg width="14" height="14" viewBox="0 0 24 24" fill="none" stroke="#fff" stroke-width="2"><path d="M5 3h4l2 5-3 2a11 11 0 0 0 6 6l2-3 5 2v4a2 2 0 0 1-2 2A17 17 0 0 1 3 5a2 2 0 0 1 2-2z"/></svg><b style="font-weight:600">+1 123 456 7890</b></div>
  <div class="f-row" style="top:278px"><svg width="14" height="12" viewBox="0 0 24 20" fill="none" stroke="#fff" stroke-width="2"><rect x="2" y="2" width="20" height="16"/><path d="M2 3l10 8 10-8"/></svg>info@haverlock.ca</div>
  <div class="f-row" style="top:304px"><svg width="14" height="16" viewBox="0 0 24 28" fill="none" stroke="#fff" stroke-width="2"><path d="M12 26s9-9 9-15a9 9 0 0 0-18 0c0 6 9 15 9 15z"/><circle cx="12" cy="11" r="3"/></svg><span>123, Building Name, Street,<br>City, State XY 123456</span></div>
  <div class="abs" style="left:141px;top:374px;width:918px;height:1px;background:#333"></div>
  <p class="abs" style="left:141px;top:396px;font-size:11px;color:#ccc">Copyright @2025 Haverlock. All Rights Reserved</p>
  <div class="social"><i></i><i></i><i></i><i></i></div>
</section>

<!-- CONTACT -->
<div class="abs contact">
  <h2 class="abs sec-title" style="left:0;width:918px;top:72px">Get In <span>Touch With Us</span></h2>
  <div class="abs divider" style="left:425px;top:134px"><i></i><b></b><i></i></div>
  <div class="field dark" style="left:117px;top:185px">Your First Name*</div>
  <div class="field" style="left:484px;top:185px">Your Last Name*</div>
  <div class="field" style="left:117px;top:254px">Enter Your Email Adress*</div>
  <div class="field" style="left:484px;top:254px">Your Phone Number*</div>
  <div class="field" style="left:117px;top:324px;width:684px;height:80px">Your Message</div>
  <div class="abs btn-gold" style="left:409px;top:442px;width:100px">Submit</div>
</div>

</body>
</html>
```